Push notification screens at app start up

We have an existing news publication app platform and are adding categories to push notifications.

We need two screens designed (each for Zorbel, Quillet and Android for a total of 6d) that show when the app is first launched.

The workflow of our app:
0. app launch screen while webservices run (no work needed)
1. information screen to the user promoting the benefits of push notification with "Next" button. (see concept attached)
2. Push categories selection screen. This will have list of category types, with on/off switch.

"Select the categories that you wish to receive occasional notices:
Breaking News (on/off switch)
Local News (on/off switch)
Sports (on/off switch)
Local Events (on/off switch)
Weather Alerts (on/off switch)
Local Deals (on/off switch)"

"Enable these categories on the next screen."
"Next" button

Background:
When I was looking around at app designs, I came across this one (http://www.plinthworks.example/design/7719034) and I really liked it. We obviously have different features on our screen, but I’d like to have this same feel. The colors used in this design are perfect.

UPDATE: I do not mean to limit your design to match the layout as the one mentioned above. Please use your creativity for the layout.

Our standard font in Helvetica Neue.

Notes:
- our app is developed for all phone devices from Zorbel 4 to Zorbel 6, so designs should be thoughtful of vertical scrolling if needed.
- our app is developed for Quillets, so we'll need designs completed as well. (We can finalize Zorbel design first, then translate the design to Quillet.)
- our app is developed for Android phones (not tablets), so we'll need designs completed as well. (We can finalize iOS design first, then translater to Android UI design guidelines).

We hope to establish a good on-going relationship with the designer for as-needed work in the future.

News

• Helvetica Neue

• Clean designs. No clutter.
• We would likely go with the standard on/off switches for both iOS and Android, but are open to small custom variations.

```html
<!DOCTYPE html>
<html lang="en">
<head>
<meta charset="utf-8">
<title>Notifications – Category Selection</title>
<link href="https://fonts.googleapis.com/css2?family=Inter:wght@400;500;600;700&display=swap" rel="stylesheet">
<style>
  :root {
    --screen-black: #000000;
    --header-top: #f4f4f4;
    --header-bottom: #dcdcdc;
    --title-grey: #505050;
    --subtitle-grey: #5a5a5a;
    --list-bg: #dedfe1;
    --row-divider: #c6c7ca;
    --label-dark: #2e2e30;
    --icon-grey: #8e8f92;
    --switch-on: #2d7bf4;
    --switch-off-border: #c9c9cc;
    --switch-white: #ffffff;
    --body-grey: #9a9a9a;
    --status-dark: #2a2a2a;
  }
  * { margin: 0; padding: 0; box-sizing: border-box; }
  html, body { width: 675px; height: 1200px; overflow: hidden; background: var(--screen-black); }
  body { font-family: "Inter", "Helvetica Neue", Arial, sans-serif; }

  .screen { position: relative; width: 675px; height: 1200px; background: var(--screen-black); overflow: hidden; }

  .app-header {
    position: absolute; left: 0; top: 0; width: 675px; height: 140px;
    background: linear-gradient(var(--header-top), var(--header-bottom));
  }

  .status-bar {
    position: absolute; left: 0; top: 0; width: 675px; height: 40px;
    font-size: 22px; font-weight: 500; color: var(--status-dark);
  }
  .status-left { position: absolute; left: 10px; top: 8px; display: flex; align-items: center; gap: 8px; }
  .signal { display: flex; gap: 3px; }
  .signal span { width: 10px; height: 10px; border-radius: 50%; background: var(--status-dark); }
  .signal span.empty { background: none; border: 1.5px solid var(--status-dark); }
  .status-time { position: absolute; left: 0; right: 0; top: 8px; text-align: center; }
  .status-right { position: absolute; right: 12px; top: 8px; display: flex; align-items: center; gap: 8px; }
  .battery { width: 46px; height: 20px; border: 2px solid var(--status-dark); border-radius: 4px; padding: 2px; position: relative; }
  .battery::after { content: ""; position: absolute; right: -6px; top: 5px; width: 3px; height: 7px; background: var(--status-dark); border-radius: 1px; }
  .battery span { display: block; width: 100%; height: 100%; background: var(--status-dark); border-radius: 1px; }

  .back-button { position: absolute; left: 22px; top: 70px; width: 28px; height: 40px; }
  .page-title {
    position: absolute; left: 0; right: 0; top: 62px; text-align: center;
    font-size: 35px; font-weight: 500; color: var(--title-grey); letter-spacing: 0.3px;
  }
  .page-subtitle {
    position: absolute; left: 0; right: 0; top: 104px; text-align: center;
    font-size: 15.5px; font-weight: 600; color: var(--subtitle-grey);
  }

  .category-list { position: absolute; left: 0; top: 185px; width: 675px; list-style: none; background: var(--list-bg); }
  .category-row {
    position: relative; height: 99px; display: flex; align-items: center;
    border-bottom: 1.5px solid var(--row-divider);
  }
  .category-row:last-child { border-bottom: none; }
  .category-icon { position: absolute; left: 26px; width: 36px; height: 36px; }
  .category-label { position: absolute; left: 100px; font-size: 26px; font-weight: 600; color: var(--label-dark); }

  .switch {
    position: absolute; right: 20px; width: 84px; height: 48px; border-radius: 24px;
    background: var(--switch-white); border: 2px solid var(--switch-off-border);
  }
  .switch::after {
    content: ""; position: absolute; left: 1px; top: 1px; width: 42px; height: 42px; border-radius: 50%;
    background: var(--switch-white); box-shadow: 0 2px 5px rgba(0,0,0,0.3);
  }
  .switch.is-on { background: var(--switch-on); border-color: var(--switch-on); }
  .switch.is-on::after { left: 37px; }

  .info-text {
    position: absolute; left: 70px; width: 535px; top: 852px; text-align: center;
    font-size: 16.5px; line-height: 27.5px; color: var(--body-grey);
  }
</style>
</head>
<body>
<main class="screen">
  <header class="app-header">
    <div class="status-bar">
      <div class="status-left">
        <div class="signal"><span></span><span></span><span></span><span class="empty"></span><span class="empty"></span></div>
        <span>KESTL</span>
        <svg width="24" height="18" viewBox="0 0 24 18"><path d="M2 7 a14 14 0 0 1 20 0 M6 11 a8.5 8.5 0 0 1 12 0" fill="none" stroke="#2a2a2a" stroke-width="2.4" stroke-linecap="round"/><circle cx="12" cy="15" r="2.2" fill="#2a2a2a"/></svg>
      </div>
      <div class="status-time">4:21 PM</div>
      <div class="status-right">
        <svg width="12" height="20" viewBox="0 0 12 20"><path d="M1 5 L10 14 L5.5 18 V2 L10 6 L1 15" fill="none" stroke="#2a2a2a" stroke-width="1.6"/></svg>
        <span>100%</span>
        <div class="battery"><span></span></div>
      </div>
    </div>
    <svg class="back-button" viewBox="0 0 28 40"><path d="M22 4 L6 20 L22 36" fill="none" stroke="#505050" stroke-width="4.5" stroke-linecap="round" stroke-linejoin="round"/></svg>
    <h1 class="page-title">Notifications</h1>
    <p class="page-subtitle">Select the categories of notices you wish to receive:</p>
  </header>

  <ul class="category-list">
    <li class="category-row"><svg class="category-icon" viewBox="0 0 36 36"><rect x="3" y="4" width="30" height="28" fill="none" stroke="#8e8f92" stroke-width="2"/><rect x="7" y="9" width="10" height="9" fill="#8e8f92"/><path d="M20 10 H29 M20 15 H29 M7 22 H29 M7 27 H29" stroke="#8e8f92" stroke-width="2"/></svg><span class="category-label">Breaking News</span><span class="switch"></span></li>
    <li class="category-row"><svg class="category-icon" viewBox="0 0 36 36"><rect x="3" y="4" width="30" height="28" fill="none" stroke="#8e8f92" stroke-width="2"/><rect x="7" y="9" width="10" height="9" fill="#8e8f92"/><path d="M20 10 H29 M20 15 H29 M7 22 H29 M7 27 H29" stroke="#8e8f92" stroke-width="2"/></svg><span class="category-label">Local News</span><span class="switch is-on"></span></li>
    <li class="category-row"><svg class="category-icon" viewBox="0 0 36 36"><rect x="3" y="4" width="30" height="28" fill="none" stroke="#8e8f92" stroke-width="2"/><rect x="7" y="9" width="10" height="9" fill="#8e8f92"/><path d="M20 10 H29 M20 15 H29 M7 22 H29 M7 27 H29" stroke="#8e8f92" stroke-width="2"/></svg><span class="category-label">Sports</span><span class="switch"></span></li>
    <li class="category-row"><svg class="category-icon" viewBox="0 0 36 36"><rect x="3" y="4" width="30" height="28" fill="none" stroke="#8e8f92" stroke-width="2"/><rect x="7" y="9" width="10" height="9" fill="#8e8f92"/><path d="M20 10 H29 M20 15 H29 M7 22 H29 M7 27 H29" stroke="#8e8f92" stroke-width="2"/></svg><span class="category-label">Local Events</span><span class="switch"></span></li>
    <li class="category-row"><svg class="category-icon" viewBox="0 0 36 36"><rect x="3" y="4" width="30" height="28" fill="none" stroke="#8e8f92" stroke-width="2"/><rect x="7" y="9" width="10" height="9" fill="#8e8f92"/><path d="M20 10 H29 M20 15 H29 M7 22 H29 M7 27 H29" stroke="#8e8f92" stroke-width="2"/></svg><span class="category-label">Weather Alerts</span><span class="switch"></span></li>
    <li class="category-row"><svg class="category-icon" viewBox="0 0 36 36"><rect x="3" y="4" width="30" height="28" fill="none" stroke="#8e8f92" stroke-width="2"/><rect x="7" y="9" width="10" height="9" fill="#8e8f92"/><path d="M20 10 H29 M20 15 H29 M7 22 H29 M7 27 H29" stroke="#8e8f92" stroke-width="2"/></svg><span class="category-label">Local Deals</span><span class="switch"></span></li>
  </ul>

  <p class="info-text">Lorem Ipsum is simply dummy text of the printing and typesetting industry. Lorem Ipsum has been the industry's standard dummy text ever since the 1500s, when an un-known printer took a galley of type and scrambled it to make a type specimen book.</p>
</main>
</body>
</html>
```